Logo, Web and Mobile Designs for enterprise social media platform

All the details are in the attached document, please start reading the scope document first which explains what is this project about and the details about the needed deliverables, after that please read the UI_Requirements document which will detail what is expected regarding the coded web version since this is a coded contest, it is very important that you meet the UI requirements or suggest something else but we will need to agree first before working on the coded version

Good Luck

Target Market(s)

Enterprise Social Media

Industry/Entity Type

Media

Coding

Coded - Design and coding required

Number of Pages Required

5+ page

Font styles to use
Sans Serif

Requirements
Must have
• All the must haves are listed in the scope document so please check before you start

```html
<!DOCTYPE html>
<html lang="en">
<head>
<meta charset="utf-8">
<title>Teamora – Enterprise Social Platform</title>
<link rel="stylesheet" href="https://fonts.googleapis.com/css2?family=Raleway:wght@400;500;600;700&family=Open+Sans:wght@400;600;700&family=Cinzel:wght@400&display=swap">
<style>
:root{
  --navy:#0f3a5f;
  --navy-dark:#0b2d4b;
  --orange:#d9772a;
  --page:#e8e9ed;
  --white:#ffffff;
  --text:#333b44;
  --muted:#7b818a;
  --line:#dfe2e6;
  --sky:#2aa6e6;
}
*{box-sizing:border-box;margin:0;padding:0}
html,body{width:1200px;height:2795px;overflow:hidden}
body{position:relative;background:var(--page);font-family:"Open Sans",sans-serif;color:var(--text)}
.abs{position:absolute}

/* header */
.site-header{left:0;top:0;width:1200px;height:95px;background:var(--white)}
.brand{left:99px;top:24px;display:flex;align-items:center;gap:14px}
.brand-mark{width:46px;height:46px;background:var(--navy)}
.brand-name{font-family:"Raleway",sans-serif;font-size:34px;font-weight:500;color:var(--navy);letter-spacing:1px}
.search{left:453px;top:30px;width:413px;height:37px;display:flex}
.search-field{flex:1;border:1px solid var(--line);border-right:none;background:#f7f8f9;font-size:13px;color:#b3b7bc;padding:9px 14px}
.search-btn{width:44px;background:var(--orange);display:flex;align-items:center;justify-content:center}
.user-pill{left:926px;top:24px;width:175px;height:48px;border:1px solid var(--navy);border-radius:26px;background:var(--white)}
.user-pill .tag{position:absolute;left:8px;top:9px;height:28px;width:118px;background:var(--navy);border-radius:14px;color:#fff;font-size:13px;display:flex;align-items:center;padding-left:26px}
.user-pill .tag:before{content:"";position:absolute;left:10px;top:10px;width:8px;height:8px;border-radius:50%;background:#3fcf6a}
.user-pill .avatar{position:absolute;right:3px;top:2px;width:42px;height:42px;border-radius:50%;background:linear-gradient(#d9c2b0,#8d7566);border:2px solid #fff}

/* nav */
.main-nav{left:0;top:95px;width:1200px;height:43px;background:var(--navy)}
.main-nav ul{list-style:none;position:absolute;left:103px;top:0;display:flex;height:43px}
.main-nav li{color:#fff;font-size:13px;line-height:43px}
.main-nav li.active{border-bottom:3px solid var(--orange)}
.nav-counts{position:absolute;left:928px;top:0;height:43px;display:flex;gap:34px;color:#fff;font-size:13px;align-items:center}
.nav-counts span{display:flex;gap:5px;align-items:center}

/* hero */
.hero{left:0;top:138px;width:1200px;height:454px;background:linear-gradient(100deg,#3a4656 0%,#8c96a4 30%,#c8ced6 50%,#6b7787 75%,#2e3846 100%)}
.hero-caption{left:615px;top:289px;width:484px;height:158px;background:rgba(120,130,145,.55);padding:38px 40px;font-family:"Cinzel",serif;color:#fff;font-size:31px;line-height:42px;letter-spacing:1px}
.hero-dots{left:566px;top:547px;display:flex;gap:8px}
.hero-dots i{width:11px;height:11px;border-radius:50%;background:#2d4a6a}
.hero-dots i:first-child{background:#fff}
.hero-badge{left:99px;top:441px;width:203px;height:202px;background:var(--white);border:2px solid #d6d9dd;display:flex;align-items:center;justify-content:center;gap:10px}
.hero-badge .sq{width:30px;height:30px;background:var(--navy)}
.hero-badge span{font-family:"Raleway",sans-serif;font-weight:600;font-size:24px;color:var(--navy)}

/* side cards */
.card{background:var(--white);box-shadow:0 1px 3px rgba(0,0,0,.12)}
.card-head{height:48px;background:#f7f9fb;border-bottom:1px solid var(--line);padding:0 12px;display:flex;align-items:center;justify-content:space-between;font-family:"Raleway",sans-serif;font-weight:600;font-size:15px;color:var(--navy)}
.card-body{padding:16px 12px 0}
.card p{font-size:11.5px;line-height:18px;color:var(--muted)}
.card-link{border-top:1px solid var(--line);margin:0 12px;padding-top:12px;text-align:right;font-size:12px;color:var(--navy);display:flex;justify-content:flex-end;align-items:center;gap:6px}
.about{left:99px;top:663px;width:365px;height:194px}
.events{left:99px;top:881px;width:365px;height:337px}
.event{display:flex;gap:8px;margin-bottom:16px}
.event .thumb{width:78px;height:96px;flex:none;background:linear-gradient(135deg,#e8ecf1,#8fa4bd)}
.event h4{font-size:12px;font-weight:600;color:#222;margin:4px 0 4px}
.event p{font-size:10.5px;line-height:16px}
.event .btn{display:inline-block;margin-top:8px;background:var(--navy);color:#fff;font-size:11px;padding:6px 18px}
.opportunities{left:99px;top:1244px;width:365px;height:382px}
.opportunities .photo{height:142px;background:linear-gradient(135deg,#3d3f43,#7c8089 55%,#2b2d31)}
.opportunities h4{font-size:12px;font-weight:600;line-height:19px;color:#222;margin:10px 0 8px}

/* profile feed */
.profile{left:99px;top:1656px;width:365px;height:669px}
.profile .cover{position:absolute;left:0;top:0;width:365px;height:265px;background:linear-gradient(120deg,#c99578 0%,#9bb0c6 45%,#3f6f95 100%)}
.profile .panel{position:absolute;left:16px;top:173px;width:336px;height:496px;background:var(--white);box-shadow:0 1px 3px rgba(0,0,0,.12)}
.profile .avatar{position:absolute;left:145px;top:132px;width:86px;height:86px;border-radius:50%;background:linear-gradient(#ccb3a0,#8b6f5e);border:3px solid #fff}
.feed-bar{position:absolute;left:65px;top:255px;width:244px;height:60px;background:var(--sky);color:#fff;display:flex;align-items:center;gap:14px;padding-left:10px}
.feed-bar .ic{width:40px;height:40px;border-radius:50%;border:2px solid #fff;flex:none}
.feed-bar b{display:block;font-family:"Raleway",sans-serif;font-weight:500;font-size:21px;line-height:22px}
.feed-bar small{font-size:11px}
.tweets{position:absolute;left:16px;top:352px;width:336px}
.tweet{padding:0 40px 0 39px;font-size:10px;line-height:15px;color:#8a9099;margin-bottom:16px}
.tweet a{color:#2a9ad6;text-decoration:none}
.tweet time{display:block;color:#333;font-size:9.5px}
.tweet.hl{background:#f4f5f6;border-left:4px solid var(--navy);padding:6px 40px 6px 35px;margin-right:70px}
.tweet .pink{color:#e0484c}
.tweet .green{color:#42a34a}

/* posts */
.feed{left:475px;top:663px;width:624px;height:1777px;background:var(--white);box-shadow:0 1px 3px rgba(0,0,0,.12)}
.post{position:absolute;left:0;width:624px}
.post h2{position:absolute;top:24px;width:100%;text-align:center;font-family:"Raleway",sans-serif;font-weight:500;font-size:21px;color:#222;letter-spacing:.3px}
.post .meta{position:absolute;top:68px;width:100%;display:flex;justify-content:center;gap:24px;font-size:11px;color:#444}
.post .meta span{display:flex;gap:4px;align-items:center}
.post .photo{position:absolute;left:6px;top:101px;width:614px;height:316px}
.post p{position:absolute;left:6px;top:440px;width:610px;font-size:11.5px;line-height:17px;color:#555}
.post .actions{position:absolute;left:4px;top:516px;width:616px;height:36px;border-top:1px solid var(--line)}
.post .more{position:absolute;left:0;top:-1px;height:36px;width:170px;border:1px solid var(--line);font-size:10px;font-weight:700;color:#333;display:flex;align-items:center;justify-content:center;letter-spacing:.3px;background:#fff}
.post .share{position:absolute;right:0;top:-1px;height:36px;width:158px;border:1px solid var(--line);background:#fff;display:flex;align-items:center;justify-content:center;gap:16px}
.post .share i{width:9px;height:9px;background:#333;display:block}
.pager{left:965px;top:2372px;display:flex;gap:6px}
.pager span{width:39px;height:39px;background:var(--orange);color:#fff;font-size:13px;display:flex;align-items:center;justify-content:center}

/* footer */
.site-footer{left:0;top:2483px;width:1200px;height:263px;background:var(--navy)}
.site-footer h3{font-family:"Raleway",sans-serif;font-weight:500;font-size:18px;color:#fff;text-transform:uppercase;margin-bottom:18px}
.newsletter{left:99px;top:44px}
.newsletter form{display:flex;width:307px;height:34px}
.newsletter .field{flex:1;background:#fff;font-size:11px;color:#aab0b7;padding:9px 14px}
.newsletter .go{width:58px;background:var(--orange);display:flex;align-items:center;justify-content:center}
.socials{display:flex;gap:34px;margin-top:48px}
.socials i{width:14px;height:14px;background:#fff;display:block}
.footer-col{top:44px}
.footer-col ul{list-style:none}
.footer-col li{color:#fff;font-size:12.5px;line-height:24px}
.quick{left:486px}
.guide{left:684px}
.footer-brand{left:900px;top:60px;display:flex;align-items:center;gap:10px;opacity:.18}
.footer-brand .sq{width:30px;height:30px;background:#fff}
.footer-brand span{font-family:"Raleway",sans-serif;font-weight:600;font-size:26px;color:#fff}
.copyright{left:0;top:2746px;width:1200px;height:49px;background:var(--navy-dark);color:#fff;font-size:12.5px;display:flex;align-items:center;justify-content:center}
</style>
</head>
<body>

<header class="site-header abs">
  <div class="brand abs"><span class="brand-mark"></span><span class="brand-name">Teamora</span></div>
  <div class="search abs">
    <div class="search-field">Enter your Keyword</div>
    <div class="search-btn"><svg width="16" height="16" viewBox="0 0 16 16"><circle cx="6.5" cy="6.5" r="4.8" fill="none" stroke="#fff" stroke-width="2"/><path d="M10 10l4.5 4.5" stroke="#fff" stroke-width="2.4"/></svg></div>
  </div>
  <div class="user-pill abs"><span class="tag">Nadia Corin</span><span class="avatar" role="img" aria-label="User portrait"></span></div>
</header>

<nav class="main-nav abs">
  <ul>
    <li class="active" style="padding:0 2px;margin-right:62px">Home</li>
    <li style="margin-right:68px">How it works</li>
    <li style="margin-right:59px">Services</li>
    <li style="margin-right:58px">Products</li>
    <li style="margin-right:47px">news</li>
    <li>Contact us</li>
  </ul>
  <div class="nav-counts">
    <span>02 <svg width="12" height="13" viewBox="0 0 12 13"><path d="M6 1a4 4 0 0 0-4 4v3L1 10h10L10 8V5a4 4 0 0 0-4-4z" fill="#fff"/><circle cx="6" cy="11.5" r="1.4" fill="#fff"/></svg></span>
    <span>07 <svg width="12" height="13" viewBox="0 0 12 13"><circle cx="6" cy="4" r="3" fill="#fff"/><path d="M0 13c0-4 3-5.5 6-5.5s6 1.5 6 5.5z" fill="#fff"/></svg></span>
    <span>00 <svg width="14" height="12" viewBox="0 0 14 12"><ellipse cx="7" cy="5" rx="7" ry="5" fill="#fff"/><path d="M3 8l-1 4 4-3z" fill="#fff"/></svg></span>
  </div>
</nav>

<section class="hero abs" role="img" aria-label="Business handshake over a desk with tablet and charts"></section>
<div class="hero-caption abs">We Serve For<br>Corporates/Enterprises</div>
<div class="hero-dots abs"><i></i><i></i><i></i><i></i></div>
<div class="hero-badge abs"><span class="sq"></span><span>Teamora</span></div>

<aside>
  <div class="card about abs">
    <div class="card-head">About Our Teamora</div>
    <div class="card-body"><p>Lorem Ipsum is simply dummy text of the printing and type-setting industry. Lorem Ipsum has been the industry's stand-ard dummy text ever since the 1500s, when an unknown printer took a galley.</p></div>
    <div class="card-link" style="margin-top:14px">READ MORE <svg width="12" height="12" viewBox="0 0 12 12"><circle cx="6" cy="6" r="6" fill="var(--navy)"/><path d="M5 3.5L7.5 6 5 8.5" stroke="#fff" stroke-width="1.6" fill="none"/></svg></div>
  </div>

  <div class="card events abs">
    <div class="card-head">Subscribe Events <svg width="14" height="14" viewBox="0 0 14 14"><path d="M3 1v11M1 10l2 3 2-3" stroke="var(--navy)" stroke-width="1.6" fill="none"/><path d="M7 3h7M7 7h5M7 11h3" stroke="var(--navy)" stroke-width="1.8"/></svg></div>
    <div class="card-body">
      <div class="event"><div class="thumb" role="img" aria-label="Event photo of a businesswoman"></div><div><h4>Lorem Ipsum is simply</h4><p>Lorem Ipsum has been the industry's standard dummy text ever since the 1500s, when an rinter</p><span class="btn">Subscribe now</span></div></div>
      <div class="event"><div class="thumb" role="img" aria-label="Event photo of a business team"></div><div><h4>Lorem Ipsum is simply</h4><p>Lorem Ipsum has been the industry's standard dummy text ever since the 1500s, when an rinter</p><span class="btn">Subscribe now</span></div></div>
    </div>
    <div class="card-link" style="margin-top:4px">ADD EVENTS <svg width="12" height="12" viewBox="0 0 12 12"><rect width="12" height="12" rx="2" fill="var(--navy)"/><path d="M6 3v6M3 6h6" stroke="#fff" stroke-width="1.6"/></svg></div>
  </div>

  <div class="card opportunities abs">
    <div class="card-head">Business Opportunities</div>
    <div class="card-body">
      <div class="photo" role="img" aria-label="Team meeting around a table seen from above"></div>
      <h4>Lorem Ipsum is simply dummy text of the printing and type-setting industry</h4>
      <p>It has survived not only five centuries, but also the leap inchanged. It was popularised in the 1960s with the release of Lorvex Lorem Ipsum passages ...</p>
    </div>
    <div class="card-link" style="margin-top:16px">CREATE OWN <svg width="13" height="11" viewBox="0 0 13 11"><rect y="2" width="13" height="9" rx="1" fill="var(--navy)"/><rect x="4" width="5" height="3" fill="none" stroke="var(--navy)" stroke-width="1.4"/></svg></div>
  </div>

  <div class="profile abs">
    <div class="cover" role="img" aria-label="Blurred office background"></div>
    <div class="panel"></div>
    <div class="avatar" role="img" aria-label="Profile portrait"></div>
    <div class="feed-bar"><span class="ic"></span><span><b>Updates</b><small>My social feed</small></span></div>
    <div class="tweets">
      <div class="tweet">Experience more with expanded posts <a>lnk.example/8gh7sq</a><time>18 hours ago</time></div>
      <div class="tweet hl">Tailored trends bring you closer <a>lnk.example/pv0hq2</a><time>12 June 2012</time></div>
      <div class="tweet">Our new nest: <a>lnk.example/6ugo6x</a><time>11 June 2012</time></div>
      <div class="tweet">Updates &amp; <span class="green">@RaceWeekly</span> are taking you to the Summit Cup 400 with <a>lnk.example/0bLmhU</a>. Read more: <a>lnk.example/i4qQUi</a><time>7 June 2012</time></div>
      <div class="tweet">Follow me <span class="pink">@marlowe</span></div>
    </div>
  </div>
</aside>

<main class="feed abs">
  <article class="post" style="top:0">
    <h2>LOREM IPSUM IS SIMPLY DUMMY TEXT</h2>
    <div class="meta"><span><svg width="10" height="10" viewBox="0 0 10 10"><rect x=".5" y="1.5" width="9" height="8" fill="none" stroke="#444"/><path d="M.5 4h9" stroke="#444"/></svg>AUGEST 06 2015</span><span><svg width="11" height="10" viewBox="0 0 11 10"><ellipse cx="5.5" cy="4.5" rx="5" ry="4" fill="none" stroke="#444"/></svg>15 COMMENT</span><span><svg width="10" height="10" viewBox="0 0 10 10"><path d="M1 4h2v6H1zM3 4l2-4c1 0 1.5.7 1.3 2L6 4h3l-1 6H3z" fill="none" stroke="#444"/></svg>121 LIKES</span></div>
    <div class="photo" role="img" aria-label="Team of colleagues reviewing documents at a laptop" style="background:linear-gradient(120deg,#e9e6df 0%,#b8c0c8 40%,#3c4a5c 75%,#e4e2dc 100%)"></div>
    <p>Sed ut perspiciatis unde omnis iste natus error sit voluptatem accusantium doloremque laudantium, totam rem aperiam, eaque ipsa quae ab illo inventore veritatis et quasi architecto beatae vitae dicta sunt explicabo. Nemo enim ipsam voluptatem quia voluptas sit aspernatur aut.</p>
    <div class="actions"><span class="more">CONTINUE READING</span><span class="share"><i></i><i></i><i></i><i></i></span></div>
  </article>

  <article class="post" style="top:555px">
    <h2>LOREM IPSUM IS SIMPLY DUMMY TEXT</h2>
    <div class="meta"><span><svg width="10" height="10" viewBox="0 0 10 10"><rect x=".5" y="1.5" width="9" height="8" fill="none" stroke="#444"/><path d="M.5 4h9" stroke="#444"/></svg>AUGEST 06 2015</span><span><svg width="11" height="10" viewBox="0 0 11 10"><ellipse cx="5.5" cy="4.5" rx="5" ry="4" fill="none" stroke="#444"/></svg>15 COMMENT</span><span><svg width="10" height="10" viewBox="0 0 10 10"><path d="M1 4h2v6H1zM3 4l2-4c1 0 1.5.7 1.3 2L6 4h3l-1 6H3z" fill="none" stroke="#444"/></svg>121 LIKES</span></div>
    <div class="photo" role="img" aria-label="Hand touching a glowing network of people figures" style="background:radial-gradient(circle at 22% 30%,#f2b35a 0%,#8a6a52 18%,#2a3a55 45%,#aab3c4 100%)"></div>
    <p>Sed ut perspiciatis unde omnis iste natus error sit voluptatem accusantium doloremque laudantium, totam rem aperiam, eaque ipsa quae ab illo inventore veritatis et quasi architecto beatae vitae dicta sunt explicabo. Nemo enim ipsam voluptatem quia voluptas sit aspernatur aut.</p>
    <div class="actions"><span class="more">CONTINUE READING</span><span class="share"><i></i><i></i><i></i><i></i></span></div>
  </article>

  <article class="post" style="top:1113px">
    <h2>LOREM IPSUM IS SIMPLY DUMMY TEXT</h2>
    <div class="meta"><span><svg width="10" height="10" viewBox="0 0 10 10"><rect x=".5" y="1.5" width="9" height="8" fill="none" stroke="#444"/><path d="M.5 4h9" stroke="#444"/></svg>AUGEST 06 2015</span><span><svg width="11" height="10" viewBox="0 0 11 10"><ellipse cx="5.5" cy="4.5" rx="5" ry="4" fill="none" stroke="#444"/></svg>15 COMMENT</span><span><svg width="10" height="10" viewBox="0 0 10 10"><path d="M1 4h2v6H1zM3 4l2-4c1 0 1.5.7 1.3 2L6 4h3l-1 6H3z" fill="none" stroke="#444"/></svg>121 LIKES</span></div>
    <div class="photo" role="img" aria-label="Presenter speaking to a seated group in a bright room" style="background:linear-gradient(180deg,#e6e8e6 0%,#c9cfcf 45%,#4a5566 75%,#2d3440 100%)"></div>
    <p>Sed ut perspiciatis unde omnis iste natus error sit voluptatem accusantium doloremque laudantium, totam rem aperiam, eaque ipsa quae ab illo inventore veritatis et quasi architecto beatae vitae dicta sunt explicabo. Nemo enim ipsam voluptatem quia voluptas sit aspernatur aut.</p>
    <div class="actions"><span class="more">CONTINUE READING</span><span class="share"><i></i><i></i><i></i><i></i></span></div>
  </article>
</main>
<div class="pager abs"><span>1</span><span>2</span><span>3</span></div>

<footer class="site-footer abs">
  <div class="newsletter abs">
    <h3>Sign up for our newsletter</h3>
    <form><div class="field">Enter your address...</div><div class="go"><svg width="18" height="18" viewBox="0 0 18 18"><circle cx="9" cy="9" r="9" fill="#fff"/><path d="M5 9h7M9 5.5L12.5 9 9 12.5" stroke="var(--orange)" stroke-width="2" fill="none"/></svg></div></form>
    <div class="socials"><i></i><i></i><i></i><i></i></div>
  </div>
  <div class="footer-col quick abs"><h3>Quick link</h3><ul><li>Home</li><li>How it works</li><li>Services</li><li>Products</li><li>news</li><li>Contact us</li></ul></div>
  <div class="footer-col guide abs"><h3>Guidelines</h3><ul><li>Branding</li><li>Components</li><li>Widgets</li></ul></div>
  <div class="footer-brand abs"><span class="sq"></span><span>Teamora</span></div>
</footer>
<div class="copyright abs">© Copyright 2015 teamora All rights reserved</div>

</body>
</html>
```